Harbourline Electrical Solutions

On one side. LOGO (underneath:) Commercial Industrial Residential

- NAME & CONTACT DETAILS

Marcus T. Hollings
Project Manager

(Cell icon) (441) 555-0187
(Email icon) hlelectricalsolutions@mailvento.com
(Facebook & Instagram icons )@hlelectricalsolutions

Other side: LOGO - underneath ELECTRICAL CONSTRUCTION & MAINTENANCE . LED LIGHTING & AUTOMATION . LIFE SAFETY SYSTEMS (FIRE ALARM / SECURITY) . DATA & COMMUNICATION

```html
<!DOCTYPE html>
<html lang="en">
<head>
<meta charset="utf-8">
<title>Harbourline Electrical Solutions – Business Card</title>
<link href="https://fonts.googleapis.com/css2?family=Montserrat:wght@500;600&family=Roboto:wght@400&family=Saira+Semi+Condensed:wght@600&display=swap" rel="stylesheet">
<style>
  :root {
    --brand-blue: #0b5878;
    --band-grey: #3e4345;
    --ink: #3a3a3a;
    --paper: #ffffff;
    --backdrop: #d9dcde;
  }
  * { margin: 0; padding: 0; box-sizing: border-box; }
  html, body { width: 799px; height: 1200px; overflow: hidden; }
  body {
    background: var(--backdrop);
    font-family: "Roboto", sans-serif;
    position: relative;
  }
  .card {
    position: absolute;
    left: 60px;
    width: 680px;
    height: 389px;
    overflow: hidden;
    box-shadow: 0 6px 18px rgba(0,0,0,.25);
  }
  .card--front { top: 130px; background: var(--brand-blue); }
  .card--back  { top: 680px; background: var(--paper); }

  /* brand wordmark */
  .wordmark {
    position: absolute;
    display: flex;
    align-items: center;
    gap: 18px;
    font-family: "Montserrat", sans-serif;
    font-weight: 600;
    text-transform: uppercase;
    line-height: 1.05;
  }
  .wordmark__square { width: 44px; height: 44px; flex: none; }
  .wordmark__name { font-size: 27px; letter-spacing: 3px; }
  .card--front .wordmark { left: 190px; top: 38px; color: var(--paper); }
  .card--front .wordmark__square { background: var(--paper); }
  .card--back .wordmark { left: 40px; top: 92px; color: var(--brand-blue); }
  .card--back .wordmark__name { font-size: 24px; letter-spacing: 2px; }
  .card--back .wordmark__square { background: var(--brand-blue); }

  /* front services band */
  .services {
    position: absolute;
    left: 0; top: 168px;
    width: 100%; height: 74px;
    background: var(--band-grey);
    color: var(--paper);
    font-size: 16px;
    padding: 13px 0 0 40px;
    line-height: 1.5;
  }
  .social {
    position: absolute;
    left: 140px; top: 268px;
    display: flex; align-items: center; gap: 6px;
    color: var(--paper);
    font-size: 19px;
  }
  .social__dot { width: 20px; height: 20px; border: 2px solid currentColor; border-radius: 50%; }
  .social__handle { margin-left: 8px; }

  /* back contact */
  .contact {
    position: absolute;
    left: 368px; top: 120px;
    color: var(--ink);
    font-size: 16px;
  }
  .contact__name {
    font-family: "Saira Semi Condensed", sans-serif;
    font-weight: 600;
    font-size: 25px;
    color: var(--brand-blue);
    line-height: 1;
  }
  .contact__role { font-size: 15px; margin-bottom: 10px; }
  .contact__list { list-style: none; }
  .contact__item { display: flex; align-items: center; gap: 10px; line-height: 1.45; }
  .contact__icon { width: 14px; height: 14px; flex: none; color: var(--brand-blue); }
  .contact__dot { width: 13px; height: 13px; border: 2px solid var(--brand-blue); border-radius: 50%; flex: none; }

  .sectors {
    position: absolute;
    left: 0; bottom: 0;
    width: 100%; height: 96px;
    background: var(--brand-blue);
    color: var(--paper);
    font-size: 15px;
    letter-spacing: 1.5px;
    padding: 30px 0 0 70px;
  }
  .sectors span { margin: 0 10px; }
</style>
</head>
<body>

<section class="card card--front" aria-label="Card front">
  <div class="wordmark">
    <div class="wordmark__square"></div>
    <div class="wordmark__name">Harbourline<br>Electrical<br>Solutions</div>
  </div>
  <div class="services">
    Electrical Construction &amp; Maintenance &nbsp;|&nbsp; Led Lighting &amp; Automation<br>
    Life Safety Systems (Fire Alarm/Security) &nbsp;|&nbsp; Data &amp; Communication
  </div>
  <div class="social">
    <span class="social__dot"></span><span class="social__dot"></span>
    <span class="social__handle">@hlelectricalsolutions</span>
  </div>
</section>

<section class="card card--back" aria-label="Card back">
  <div class="wordmark">
    <div class="wordmark__square"></div>
    <div class="wordmark__name">Harbourline<br>Electrical<br>Solutions</div>
  </div>
  <div class="contact">
    <div class="contact__name">Marcus T. Hollings</div>
    <div class="contact__role">Project Manager</div>
    <ul class="contact__list">
      <li class="contact__item">
        <svg class="contact__icon" viewBox="0 0 16 16" aria-hidden="true"><path fill="currentColor" d="M3 1h3l1.5 4-2 1.3a9 9 0 0 0 4.2 4.2L11 8.5l4 1.5v3a2 2 0 0 1-2 2A12 12 0 0 1 1 3a2 2 0 0 1 2-2z"/></svg>
        (441) 555-0187
      </li>
      <li class="contact__item">
        <svg class="contact__icon" viewBox="0 0 16 16" aria-hidden="true"><rect x="1" y="3" width="14" height="10" fill="currentColor"/><path d="M1.5 3.5 8 9l6.5-5.5" stroke="#fff" stroke-width="1.3" fill="none"/></svg>
        hlelectricalsolutions@mailvento.com
      </li>
      <li class="contact__item"><span class="contact__dot"></span>@hlelectricalsolutions</li>
      <li class="contact__item"><span class="contact__dot"></span>@hlelectricalsolutions</li>
    </ul>
  </div>
  <div class="sectors">COMMERCIAL<span>|</span>INDUSTRIAL<span>|</span>RESIDENTIAL</div>
</section>

</body>
</html>
```